Create an awesome website for a medical clinic

This is a new website for a doctor's office. The site should be clean and modern, easy to navigate.

This is a wellness clinic, we want to help our clients have a healthy, active lifestyle. It should be friendly and inviting, and easy for them to call or schedule an appointment.

The site should be responsive and designed using the attached Bootstrap 3 PSD.

We will provide stock photos, until then please use stock photos from:

pixelharbor.com or
framequarry.com (preferred)

Some example sites of clean and modern designs that we like:

https://tulsaspinecare.com/
http://reachpastjoints.com/
http://turninghealthier.com/

Also attached is a temporary logo you can use.

Reason: Thank you everyone for your great designs - we need a little more time so I'm extending the project.

Need extra days to review

Also, the colors in the new logo I just linked to are the final colors of the logo, so feel free to use any complimentary colors to it.

Hi everyone, The boss wants to change the layout of the site a little bit - here's the revised layout: https://www.filecrate.com/s/k9rt31vx2qp84zn/notes%2011_29_2017.pdf?dl=0 And the graphic assets you can use are here: https://www.filecrate.com/s/k9rt31vx2qp84zn/notes%2011_29_2017.pdf?dl=0 Feel free to change the background color of the "topbar", and change the icons of the "why people trust us" if you want, these are just temporary placeholders. Thanks for your patience and hard work!

Target Market(s)

People seeking medical treatment (wellness clinic)

Industry/Entity Type

Doctor

Number of Pages Required

1 page

Font styles to use
Sans Serif

Colors
0592cd
33a6d7
abd037
9bcb3c

Requirements
Must have
• The home page should have: a strong hero image/slideshow, clinic phone number should be prominent and at the top of the page (in the nav), a "what to expect" section (this is like a FAQs section - see attachment), and a strong call to action (a button to call or schedule an appointment).
• The what to expect section is useful so that prospective clients can determine if we're a good fit for them or not. It's a basic, first-step pre-qualification block of information.
• Social media icons which links to our social media profiles should be included.
Nice to have
• - Link to 3 most recent blog entries
• - Testimonials
• - How a multilevel nav menu looks.

```html
<!DOCTYPE html>
<html lang="en">
<head>
<meta charset="utf-8">
<title>Fern Medical Clinic</title>
<link href="https://fonts.googleapis.com/css2?family=Lato:ital,wght@0,400;0,700;0,900;1,400;1,700&display=swap" rel="stylesheet">
<style>
:root{
  --blue:#0592cd;
  --blue-light:#33a6d7;
  --green:#abd037;
  --green-deep:#9bcb3c;
  --green-bar:#8fbf2c;
  --logo-green:#3aa935;
  --ink:#222;
  --muted:#777;
  --white:#fff;
}
*{box-sizing:border-box;margin:0;padding:0}
html,body{width:1200px;height:3462px;overflow:hidden}
body{font-family:'Lato',sans-serif;color:var(--ink);background:var(--white);position:relative}
section,header,footer{position:absolute;left:0;width:1200px}
.abs{position:absolute}

/* Header */
.site-header{top:0;height:98px;background:var(--white);z-index:2}
.brand{left:116px;top:14px;font-weight:900;font-size:40px;line-height:40px;color:var(--logo-green);width:220px}
.brand small{display:block;font-size:17px;line-height:22px;font-weight:900;letter-spacing:.5px}
.main-nav{left:320px;top:0;display:flex;height:98px;align-items:center}
.main-nav a{font-size:17px;color:#666;text-decoration:none;padding:0 18px;height:98px;line-height:98px;position:relative}
.main-nav a.active{color:var(--green-deep)}
.main-nav a.active::after{content:"";position:absolute;left:6px;right:6px;bottom:0;height:4px;background:var(--green-deep)}
.nav-phone{left:905px;top:34px;font-size:21px;font-weight:700;color:#111;display:flex;align-items:center;gap:8px}

/* Hero */
.hero{top:98px;height:525px;overflow:hidden}
.hero-photo{position:absolute;inset:0;background:linear-gradient(180deg,#a9c6d6 0%,#c9d7c2 40%,#7ea64a 75%,#5d8c2e 100%)}
.hero-title{left:0;width:1200px;top:176px;text-align:center;color:var(--white);font-weight:700;font-size:37px;line-height:48px;letter-spacing:1px;text-transform:uppercase}
.btn-outline-light{left:438px;top:283px;width:321px;height:51px;border:2px solid var(--white);color:var(--white);font-size:20px;font-weight:700;display:flex;align-items:center;justify-content:center;background:rgba(255,255,255,.08)}
.hero-dots{left:0;width:1200px;top:490px;display:flex;justify-content:center;gap:9px}
.hero-dots span{width:14px;height:14px;border-radius:50%;background:var(--white);border:2px solid #333}
.hero-dots span:first-child{background:#333;border-color:var(--white)}

/* Welcome */
.welcome{top:623px;height:477px;overflow:hidden}
.welcome-art{left:460px;top:0;width:740px;height:477px}
.welcome-copy{position:absolute;left:134px;top:0;width:500px;height:477px;z-index:1}
.welcome-copy h1{position:absolute;left:0;top:78px;font-size:33px;font-weight:700;color:#111;white-space:nowrap}
.welcome-copy .lead{position:absolute;left:0;top:138px;width:470px;font-size:16px;line-height:25px;color:var(--muted)}
.welcome-copy .body{position:absolute;left:0;top:206px;width:480px;font-size:14px;line-height:24px;color:var(--muted)}
.btn-blue{position:absolute;left:0;top:328px;width:173px;height:46px;background:linear-gradient(180deg,var(--blue-light),var(--blue));color:var(--white);font-weight:700;font-size:16px;display:flex;align-items:center;justify-content:center;border-radius:2px}

/* What to expect */
.expect{top:1100px;height:580px;background:linear-gradient(120deg,var(--blue) 0%,var(--blue-light) 40%,#6bbf8e 70%,var(--green) 100%)}
.expect h2{left:0;width:1200px;top:46px;text-align:center;color:var(--white);font-size:33px;font-weight:400}
.accordion{left:210px;top:123px;width:792px}
.acc-open-head{height:49px;background:var(--white);display:flex;align-items:center;justify-content:space-between;padding:0 26px;color:var(--blue);font-weight:700;font-size:17px}
.acc-body{height:113px;background:rgba(20,90,120,.35);padding:16px 30px;color:#eaf4f8;font-size:15px;line-height:24px}
.acc-item{height:49px;border:2px solid var(--white);border-top-width:0;display:flex;align-items:center;justify-content:space-between;padding:0 26px;color:var(--white);font-weight:700;font-size:16px}
.acc-item.first{margin-top:18px;border-top-width:2px}

/* Blogs */
.blogs{top:1680px;height:480px}
.blogs h2{left:124px;top:40px;font-size:33px;font-weight:400;color:#111}
.blog-card{top:116px;width:303px;height:346px;border:1px solid #ddd;background:var(--white);box-shadow:0 1px 3px rgba(0,0,0,.08)}
.blog-photo{position:absolute;left:0;top:0;width:301px;height:196px}
.blog-date{position:absolute;left:0;top:143px;width:60px;height:58px;background:var(--green-deep);color:var(--white);text-align:center;font-size:26px;line-height:30px;padding-top:4px}
.blog-date small{display:block;font-size:13px;line-height:16px}
.blog-card h3{position:absolute;left:24px;top:216px;font-size:17px;font-weight:400;color:#222}
.blog-card p{position:absolute;left:24px;top:244px;width:250px;font-size:11px;line-height:17px;color:#888}
.blog-card .more{position:absolute;left:24px;top:305px;font-size:11px;color:var(--blue);font-weight:700}

/* Testimonials */
.testimonials{top:2146px;height:474px;overflow:hidden}
.testimonials svg.bg{position:absolute;left:0;top:0}
.testimonials h2{left:0;width:1200px;top:132px;text-align:center;color:var(--white);font-size:31px;font-weight:400}
.quote-mark{left:0;width:1200px;top:186px;text-align:center;color:var(--white);font-size:96px;font-weight:900;line-height:80px;font-family:Georgia,serif}
.testimonial-text{left:250px;width:700px;top:262px;text-align:center;color:var(--white);font-style:italic;font-size:12px;line-height:21px}
.testimonial-name{left:0;width:1200px;top:350px;text-align:center;color:var(--white);font-style:italic;font-weight:700;font-size:15px}
.t-dots{left:0;width:1200px;top:392px;display:flex;justify-content:center;gap:4px}
.t-dots span{width:22px;height:3px;background:rgba(255,255,255,.5)}
.t-dots span:first-child{background:var(--white)}

/* Why choose us */
.why{top:2620px;height:445px}
.video-frame{left:116px;top:72px;width:453px;height:290px;border:4px solid #eee;box-shadow:0 1px 4px rgba(0,0,0,.15)}
.video-photo{position:absolute;inset:0;background:linear-gradient(135deg,#d9d2cc 0%,#eee9e3 50%,#c9c2bb 100%)}
.play{position:absolute;left:190px;top:108px;width:70px;height:70px;border-radius:50%;background:var(--white)}
.why h2{left:605px;top:64px;font-size:31px;font-weight:400;color:#111}
.why .lead{left:605px;top:124px;width:480px;font-size:16px;line-height:25px;color:var(--muted)}
.why .body{left:605px;top:190px;width:480px;font-size:14px;line-height:24px;color:var(--muted)}
.btn-outline-blue{left:605px;top:293px;width:159px;height:44px;border:2px solid var(--blue);color:var(--blue);font-weight:700;font-size:15px;display:flex;align-items:center;justify-content:center}

/* Footer */
.site-footer{top:3065px;height:323px;background:var(--green)}
.foot-col{top:55px;color:var(--white)}
.foot-col h4{font-size:18px;font-weight:400;letter-spacing:.5px;margin-bottom:18px;text-transform:uppercase}
.foot-col li{list-style:none;font-size:14px;line-height:32px}
.contact-line{display:flex;align-items:center;gap:8px;font-size:14px;line-height:32px;white-space:nowrap}
.socials{display:flex;gap:10px;margin-top:2px}
.socials span{width:34px;height:34px;border-radius:50%;border:2px solid var(--white)}
.legal{position:absolute;left:0;width:1200px;top:3388px;height:74px;background:var(--green-bar);color:var(--white);font-size:11px;display:flex;align-items:center;justify-content:center}
</style>
</head>
<body>

<header class="site-header">
  <div class="brand abs">FERN<small>MEDICAL CLINIC</small></div>
  <nav class="main-nav abs">
    <a class="active">Home</a><a>About Us</a><a>Services</a><a>Testimonial</a><a>FAQ</a><a>Contact</a>
  </nav>
  <div class="nav-phone abs">
    <svg width="20" height="20" viewBox="0 0 24 24"><path fill="#0592cd" d="M6.6 10.8a15 15 0 0 0 6.6 6.6l2.2-2.2c.3-.3.7-.4 1-.2 1.1.4 2.3.6 3.6.6.6 0 1 .4 1 1V20c0 .6-.4 1-1 1A17 17 0 0 1 3 4c0-.6.4-1 1-1h3.5c.6 0 1 .4 1 1 0 1.3.2 2.5.6 3.6.1.3 0 .7-.2 1z"/></svg>
    (633) 555 0182
  </div>
</header>

<section class="hero">
  <div class="hero-photo" role="img" aria-label="Woman in white top stretching outdoors on green grass"></div>
  <h1 class="hero-title abs">Medical Wellness Clinic for<br>a Health Lifestyle</h1>
  <div class="btn-outline-light abs">Schedule an Appointment</div>
  <div class="hero-dots abs"><span></span><span></span><span></span><span></span></div>
</section>

<section class="welcome">
  <svg class="welcome-art abs" viewBox="0 0 740 477" role="img" aria-label="Smiling woman in blue top stretching against a bright sky">
    <defs>
      <linearGradient id="sky" x1="0" y1="0" x2="0" y2="1">
        <stop offset="0" stop-color="#5fa6d8"/><stop offset=".55" stop-color="#b9d7ec"/><stop offset="1" stop-color="#e9f2f8"/>
      </linearGradient>
    </defs>
    <path d="M210 0 H740 V477 H12 C180 380 290 180 210 0 Z" fill="url(#sky)"/>
    <path d="M196 0 C280 180 170 380 0 477" fill="none" stroke="#9bcb3c" stroke-width="7"/>
  </svg>
  <div class="welcome-copy">
    <h1>Welcome to Fern Medical Clinic</h1>
    <p class="lead">Vivamus porttitor purus nisi eleifend libero a tempus libero lectus feugiat felis Morbi diam mauris viverra</p>
    <p class="body">ligula pulvinar metus eget consectetuer augue nisi quis lacus Ut ac mi quis lacus mollis aliquam Curabitur iaculis tempus eros Curabitur vel mi sit amet magna malesuada ultrices Ut nisi erat fermentum vel congue id euismod in elit Fusce ultricies orci ac</p>
    <div class="btn-blue">Learn More</div>
  </div>
</section>

<section class="expect">
  <h2 class="abs">What to Expect</h2>
  <div class="accordion abs">
    <div class="acc-open-head">Nam cursus Morbi ut mi Nullam enim leo egestas ?
      <svg width="18" height="12" viewBox="0 0 18 12"><path d="M2 10 L9 3 L16 10" fill="none" stroke="#9bcb3c" stroke-width="3"/></svg></div>
    <div class="acc-body">Mauris vel lacus vitae felis vestibulum volutpat Etiam est nunc venenatis in tristique eu imperdiet ac nisl Cum sociis natoque penatibus et magnis dis parturient montes nascetur ridiculus mus In iaculis facilisis massa Etiam eu urna Sed porta Suspendisse quam leo molestie sed</div>
    <div class="acc-item first">Mauris vel lacus vitae felis vestibulum volutpat ?
      <svg width="18" height="12" viewBox="0 0 18 12"><path d="M2 2 L9 9 L16 2" fill="none" stroke="#fff" stroke-width="3"/></svg></div>
    <div class="acc-item">Vivamus porttitor purus nisi eleifend libero a tempus libero lectus feugiat felis ?
      <svg width="18" height="12" viewBox="0 0 18 12"><path d="M2 2 L9 9 L16 2" fill="none" stroke="#fff" stroke-width="3"/></svg></div>
    <div class="acc-item">Ut velit enim vestibulum non fermentum ?
      <svg width="18" height="12" viewBox="0 0 18 12"><path d="M2 2 L9 9 L16 2" fill="none" stroke="#fff" stroke-width="3"/></svg></div>
    <div class="acc-item">Aenean porttitor eros vel dolor Donec convallis pede ?
      <svg width="18" height="12" viewBox="0 0 18 12"><path d="M2 2 L9 9 L16 2" fill="none" stroke="#fff" stroke-width="3"/></svg></div>
  </div>
</section>

<section class="blogs">
  <h2 class="abs">Latest Blogs</h2>
  <article class="blog-card abs" style="left:122px">
    <div class="blog-photo" role="img" aria-label="Patients stretching on treatment tables in a bright clinic" style="background:linear-gradient(160deg,#d7e4ec,#b9c9d3)"></div>
    <div class="blog-date">02<small>AUG</small></div>
    <h3>Your Blog Tittle here</h3>
    <p>netus et malesuada fames ac turpis egestas. Cras id elit integer quis urna Ut ante enim dapibus malesuada fringilla eu cond</p>
    <span class="more">READ MORE</span>
  </article>
  <article class="blog-card abs" style="left:445px">
    <div class="blog-photo" role="img" aria-label="Woman relaxing outdoors among green trees" style="background:linear-gradient(160deg,#7fae45,#c6dca0)"></div>
    <div class="blog-date">02<small>AUG</small></div>
    <h3>Your Blog Tittle here</h3>
    <p>netus et malesuada fames ac turpis egestas. Cras id elit integer quis urna Ut ante enim dapibus malesuada fringilla eu cond</p>
    <span class="more">READ MORE</span>
  </article>
  <article class="blog-card abs" style="left:773px">
    <div class="blog-photo" role="img" aria-label="Therapist treating a patient lying on a clinic table" style="background:linear-gradient(160deg,#c9b7a6,#e8ddd2)"></div>
    <div class="blog-date">02<small>AUG</small></div>
    <h3>Your Blog Tittle here</h3>
    <p>netus et malesuada fames ac turpis egestas. Cras id elit integer quis urna Ut ante enim dapibus malesuada fringilla eu cond</p>
    <span class="more">READ MORE</span>
  </article>
</section>

<section class="testimonials">
  <svg class="bg" width="1200" height="474" viewBox="0 0 1200 474" role="img" aria-label="Patient receiving physical therapy in a treatment room, blue tint">
    <defs>
      <linearGradient id="tblue" x1="0" y1="0" x2="1" y2="1">
        <stop offset="0" stop-color="#0592cd"/><stop offset="1" stop-color="#33a6d7"/>
      </linearGradient>
    </defs>
    <rect width="1200" height="474" fill="url(#tblue)"/>
    <path d="M0 0 H1200 V40 C900 110 450 110 0 0 Z" fill="#fff"/>
  </svg>
  <h2 class="abs">Testimonials</h2>
  <div class="quote-mark abs">&#8221;</div>
  <svg class="abs" style="left:213px;top:214px" width="60" height="60"><path d="M2 58 V2 H58" fill="none" stroke="#fff" stroke-width="3"/></svg>
  <svg class="abs" style="left:935px;top:320px" width="60" height="60"><path d="M2 58 H58 V2" fill="none" stroke="#fff" stroke-width="3"/></svg>
  <p class="testimonial-text abs">" Sed ut perspiciatis unde omnis iste natus error sit voluptatem accusantium doloremque laudantium, totam rem aperiam, eaque ipsa quae ab illo inventore veritatis et quasi architecto beatae vitae dicta sunt explicabo. Nemo enim ipsam voluptatem quia voluptas sit aspernatur aut odit aut fugit, sed quia consequuntur .</p>
  <div class="testimonial-name abs">Jane Rowe - Maple Ridge Credit Union</div>
  <div class="t-dots abs"><span></span><span></span><span></span></div>
</section>

<section class="why">
  <div class="video-frame abs">
    <div class="video-photo" role="img" aria-label="Therapist massaging a patient's leg in a bright treatment room"></div>
    <div class="play"><svg width="70" height="70" viewBox="0 0 70 70"><path d="M29 23 L49 35 L29 47 Z" fill="#111"/></svg></div>
  </div>
  <h2 class="abs">Why Choose Us</h2>
  <p class="lead abs">Vivamus porttitor purus nisi eleifend libero a tempus libero lectus feugiat felis Morbi diam mauris viverra</p>
  <p class="body abs">ligula pulvinar metus eget consectetuer augue nisi quis lacus Ut ac mi quis lacus mollis aliquam Curabitur iaculis tempus eros Curabitur vel mi sit amet magna malesuada ultrices</p>
  <div class="btn-outline-blue abs">Learn More</div>
</section>

<footer class="site-footer">
  <div class="foot-col abs" style="left:122px">
    <h4>Quick Links</h4>
    <ul><li>Home</li><li>About Us</li><li>Why Us</li><li>What to expect</li></ul>
  </div>
  <div class="foot-col abs" style="left:347px">
    <h4>Resources</h4>
    <ul><li>Our Services</li><li>Testimonials</li><li>Our Blogs</li><li>Contact Us</li></ul>
  </div>
  <div class="foot-col abs" style="left:560px">
    <h4>Contact Info</h4>
    <div class="contact-line"><svg width="14" height="16" viewBox="0 0 14 16"><path d="M7 1a5 5 0 0 1 5 5c0 4-5 9-5 9S2 10 2 6a5 5 0 0 1 5-5z" fill="none" stroke="#fff" stroke-width="1.5"/><circle cx="7" cy="6" r="1.8" fill="#fff"/></svg>42 Birchwood Ave #3 Tulsa OK 74103</div>
    <div class="contact-line"><svg width="14" height="14" viewBox="0 0 24 24"><path fill="none" stroke="#fff" stroke-width="2" d="M6.6 10.8a15 15 0 0 0 6.6 6.6l2.2-2.2c.3-.3.7-.4 1-.2 1.1.4 2.3.6 3.6.6.6 0 1 .4 1 1V20c0 .6-.4 1-1 1A17 17 0 0 1 3 4c0-.6.4-1 1-1h3.5c.6 0 1 .4 1 1 0 1.3.2 2.5.6 3.6.1.3 0 .7-.2 1z"/></svg>586.555.0147</div>
    <div class="contact-line"><svg width="16" height="12" viewBox="0 0 16 12"><rect x="1" y="1" width="14" height="10" fill="none" stroke="#fff" stroke-width="1.5"/><path d="M1 1 L8 7 L15 1" fill="none" stroke="#fff" stroke-width="1.5"/></svg>info@companyname.com</div>
  </div>
  <div class="foot-col abs" style="left:903px">
    <h4>Follow Us</h4>
    <div class="socials"><span></span><span></span><span></span><span></span></div>
  </div>
</footer>
<div class="legal">© 2017 Company Name. All right reserved. Terms of Use</div>

</body>
</html>
```